Business Card for premium dental clinic

We are a premium dental clinic based in Brasov, Romania with more than 15 year on the market, providing quality dental treatment made by a team of more specialized dentists, working with modern equipment as a solution to beautiful and healthy teeth.

Our current logo for the clinic use 2 square with colors black and gold - dr Ternisu - studio, using family fonts Bodoni, Myriad Pro and Segoe Print.
Depending on the printing we used some gold CMYK background or gold foil picture background or a gold gradient.
We want a business card:
- eye catching business card
- distinguished business card
- premium design
- to keep the color scheme of black and gold
- to attract the customers to spent time reading the information
- modern concept

```html
<!DOCTYPE html>
<html lang="en">
<head>
<meta charset="utf-8">
<title>Corvina Dental Clinic – Business Card</title>
<link rel="stylesheet" href="https://fonts.googleapis.com/css2?family=Fira+Sans+Condensed:wght@300&family=Montserrat:wght@400;500&display=swap">
<style>
  :root {
    --backdrop: #2b231f;
    --card: #2f3033;
    --card-shade: #28292c;
    --gold: #c9a227;
    --logo-tone: #1d1e20;
    --name-light: #b9babc;
    --name-soft: #8d8e91;
    --contact: #e4e4e4;
    --divider: #6c6d70;
  }
  * { margin: 0; padding: 0; box-sizing: border-box; }
  html, body { width: 1200px; height: 800px; overflow: hidden; }
  body {
    background: var(--backdrop);
    display: flex;
    align-items: center;
    justify-content: center;
    gap: 40px;
  }
  .card {
    width: 530px;
    height: 303px;
    background: linear-gradient(160deg, var(--card) 0%, var(--card-shade) 100%);
    border: 2px solid var(--gold);
    position: relative;
    box-shadow: 0 14px 30px rgba(0,0,0,.45);
  }
  /* Front */
  .card--front { display: flex; align-items: center; padding-left: 70px; }
  .clinic-name {
    font-family: "Montserrat", sans-serif;
    font-weight: 500;
    color: var(--logo-tone);
    line-height: 1;
  }
  .clinic-name__word { display: block; font-size: 64px; letter-spacing: 1px; }
  .clinic-name__sub { display: block; font-size: 12px; letter-spacing: 3px; margin-top: 8px; padding-left: 4px; }
  /* Back */
  .card--back { display: flex; align-items: center; padding-left: 62px; }
  .doctor-name {
    font-family: "Fira Sans Condensed", sans-serif;
    font-weight: 300;
    color: var(--name-light);
    font-size: 46px;
    letter-spacing: .5px;
    white-space: nowrap;
  }
  .doctor-name__title { font-size: 30px; color: var(--name-soft); margin-right: 6px; }
  .divider {
    width: 1px;
    height: 88px;
    background: var(--divider);
    margin: 0 26px 0 26px;
  }
  .contact-list { list-style: none; font-family: "Montserrat", sans-serif; font-size: 13px; color: var(--contact); }
  .contact-list li { display: flex; align-items: center; gap: 9px; line-height: 22px; white-space: nowrap; }
  .contact-list svg { width: 12px; height: 12px; fill: var(--name-light); flex: none; }
</style>
</head>
<body>
  <section class="card card--front" aria-label="Card front">
    <p class="clinic-name">
      <span class="clinic-name__word">corvina</span>
      <span class="clinic-name__sub">DENTAL CLINIC</span>
    </p>
  </section>

  <section class="card card--back" aria-label="Card back">
    <h1 class="doctor-name"><span class="doctor-name__title">dr.</span>ternisu</h1>
    <div class="divider"></div>
    <ul class="contact-list">
      <li>
        <svg viewBox="0 0 24 24" aria-hidden="true"><path d="M6.6 10.8a15.1 15.1 0 0 0 6.6 6.6l2.2-2.2a1 1 0 0 1 1-.25 11.4 11.4 0 0 0 3.6.57 1 1 0 0 1 1 1V20a1 1 0 0 1-1 1A17 17 0 0 1 3 4a1 1 0 0 1 1-1h3.5a1 1 0 0 1 1 1c0 1.25.2 2.45.57 3.57a1 1 0 0 1-.25 1z"/></svg>
        268-410-7350
      </li>
      <li>
        <svg viewBox="0 0 24 24" aria-hidden="true"><path d="M2 5h20v14H2zm2 2v.5l8 5 8-5V7l-8 5z"/></svg>
        hello@corvinadental.ro
      </li>
      <li>
        <svg viewBox="0 0 24 24" aria-hidden="true"><circle cx="12" cy="12" r="10"/></svg>
        www.corvinadental.ro
      </li>
    </ul>
  </section>
</body>
</html>
```